Brightfen Business Card Redesign & Logo Update

We need to update our business cards to something more modern and fresh. Brightfen can provide the current color schemes and old design examples, but welcome creativity in helping us with this redesign. PLEASE NOTE that we no longer utilize the "tree" and/or "leaf" imagery in our branding. If able would apprecaite an update on the quality of our "words only" logo in Ai. / PNG formats too.

Target Market(s)

Investors, landowners, corporate partners, contractors

Industry/Entity Type

Environmental Restoration & Conservation

Contact Information for Business Card

Logo, persons name, title, mailing address, phone and email, website url

Font styles to use
Other font styles liked:
• Merriweather

Requirements
Nice to have
• Logo, persons name, title, mailing address, phone and email, website url, but open to ideams
Should not have
• No all back backgrounds

```html
<!DOCTYPE html>
<html lang="en">
<head>
<meta charset="utf-8">
<title>Brightfen Business Card</title>
<link rel="stylesheet" href="https://fonts.googleapis.com/css2?family=Merriweather:wght@400;700;900&display=swap">
<style>
  :root {
    --bg: #e6e7e9;
    --card: #ffffff;
    --orange: #f07f1f;
    --green: #1a7a3c;
    --ink: #222222;
    --shadow: rgba(0, 0, 0, 0.18);
  }
  * { margin: 0; padding: 0; box-sizing: border-box; }
  html, body {
    width: 1200px;
    height: 1059px;
    overflow: hidden;
    background: var(--bg);
    font-family: "Merriweather", Georgia, serif;
    color: var(--ink);
  }
  .sheet {
    width: 1200px;
    height: 1059px;
    display: flex;
    flex-direction: column;
    align-items: center;
    justify-content: center;
    gap: 40px;
  }
  .card {
    position: relative;
    width: 840px;
    height: 480px;
    background: var(--card);
    box-shadow: 0 10px 30px var(--shadow);
  }
  .card-front {
    display: flex;
    align-items: center;
    justify-content: center;
  }
  .wordmark {
    font-weight: 900;
    color: var(--green);
    letter-spacing: 1px;
    text-transform: uppercase;
  }
  .card-front .wordmark { font-size: 78px; }
  .card-back .wordmark {
    position: absolute;
    top: 62px;
    right: 58px;
    font-size: 40px;
  }
  .contact-block {
    position: absolute;
    left: 60px;
    bottom: 52px;
  }
  .person-name {
    font-size: 30px;
    font-weight: 700;
    text-transform: uppercase;
    letter-spacing: 0.5px;
  }
  .first-name { color: var(--orange); }
  .last-name { color: var(--green); }
  .person-title {
    font-size: 20px;
    margin-top: 4px;
  }
  .address {
    font-size: 20px;
    line-height: 1.4;
    margin-top: 44px;
    font-style: normal;
  }
  .contact-list {
    list-style: none;
    margin-top: 34px;
    font-size: 20px;
    line-height: 1.5;
  }
  .contact-list li {
    display: flex;
    align-items: center;
    gap: 12px;
  }
  .contact-icon {
    width: 18px;
    height: 18px;
    fill: var(--orange);
    flex-shrink: 0;
  }
</style>
</head>
<body>
<main class="sheet">
  <section class="card card-front">
    <div class="wordmark">Brightfen</div>
  </section>

  <section class="card card-back">
    <div class="wordmark">Brightfen</div>
    <div class="contact-block">
      <h1 class="person-name"><span class="first-name">Marcus</span> <span class="last-name">Hale</span></h1>
      <p class="person-title">Founder</p>
      <address class="address">Main Office Address<br>Road No. 48, PO 2210, BD</address>
      <ul class="contact-list">
        <li>
          <svg class="contact-icon" viewBox="0 0 24 24" aria-hidden="true"><path d="M6.6 10.8a15.1 15.1 0 0 0 6.6 6.6l2.2-2.2c.3-.3.7-.4 1-.2 1.1.4 2.3.6 3.6.6.6 0 1 .4 1 1V20c0 .6-.4 1-1 1C10.6 21 3 13.4 3 4c0-.6.4-1 1-1h3.5c.6 0 1 .4 1 1 0 1.2.2 2.4.6 3.6.1.3 0 .7-.2 1z"/></svg>
          (555) 014-2288
        </li>
        <li>
          <svg class="contact-icon" viewBox="0 0 24 24" aria-hidden="true"><path d="M2 5h20v14H2z M2 5l10 8 10-8" fill="var(--orange)"/><path d="M3 6l9 7 9-7" fill="none" stroke="#fff" stroke-width="1.6"/></svg>
          hello@brightfenco.com
        </li>
        <li>
          <svg class="contact-icon" viewBox="0 0 24 24" aria-hidden="true"><circle cx="12" cy="12" r="10"/><path d="M2 12h20M12 2c3 3 3 17 0 20M12 2c-3 3-3 17 0 20" fill="none" stroke="#fff" stroke-width="1.4"/></svg>
          www.brightfenco.com
        </li>
      </ul>
    </div>
  </section>
</main>
</body>
</html>
```